Harborline Renewal Business Card Design

Professional and clean design. The design colors should flow with the logo. Two-sided card with the website on the back which is:

www.HarborlineRenewal.example.

"Specializing in Water Damage Restoration"

On the front I need the name, email, phone, and logo.

Name: Darnell Quisby
Email: Darnell@HarborlineRenewal.example
Phone: 555-318-2046 for now

I only have the Preview and Thumbnail right now but should have the source files uploaded within a day or two.

Target Market(s)

Flood victims, home owners with water damage from busted pipes etc...

Industry/Entity Type

Business

Contact Information for Business Card

Name: Darnell Quisby

Font styles to use
Serif
Sans Serif

Requirements
Must have
• Business Card Details Info

```html
<!DOCTYPE html>
<html lang="en">
<head>
<meta charset="utf-8">
<title>Harborline Renewal Business Card</title>
<link rel="stylesheet" href="https://fonts.googleapis.com/css2?family=Cinzel:wght@600&family=Open+Sans:wght@400;700&display=swap">
<style>
  :root {
    --bg: #2b2b2d;
    --card: #050607;
    --sky: #4cc0f0;
    --ocean: #1f8fd6;
    --deep: #1b6fb0;
    --ink: #ffffff;
    --rule: #3a3f45;
  }
  * { margin: 0; padding: 0; box-sizing: border-box; }
  html, body { width: 1200px; height: 900px; overflow: hidden; background: var(--bg); }
  .canvas { position: relative; width: 1200px; height: 900px; }
  .card {
    position: absolute; width: 620px; height: 354px;
    background: var(--card); border-radius: 22px; overflow: hidden;
    box-shadow: 0 18px 40px rgba(0,0,0,.55);
  }
  .card--back { left: 60px; top: 70px; }
  .card--front { left: 520px; top: 476px; }
  .wave { position: absolute; inset: 0; width: 100%; height: 100%; }

  .brand { position: absolute; left: 0; right: 0; top: 40px; text-align: center; }
  .brand__mark {
    width: 60px; height: 60px; border-radius: 50%;
    background: var(--sky); margin: 0 auto 12px;
  }
  .brand__name {
    font-family: "Cinzel", serif; font-weight: 600; font-size: 32px; line-height: 40px;
    color: var(--sky); letter-spacing: 2px; text-transform: uppercase;
  }
  .brand__tagline {
    margin-top: 6px; font-family: "Open Sans", sans-serif; font-size: 14px; line-height: 20px;
    color: var(--ocean); text-transform: uppercase; letter-spacing: .5px;
  }
  .website {
    position: absolute; left: 40px; bottom: 14px;
    font-family: "Open Sans", sans-serif; font-size: 17px; line-height: 24px; color: var(--ink);
  }

  .front-brand { position: absolute; left: 36px; top: 60px; width: 230px; text-align: center; }
  .front-brand__mark { width: 150px; height: 150px; border-radius: 50%; background: var(--sky); margin: 0 auto 14px; }
  .front-brand__name {
    font-family: "Cinzel", serif; font-weight: 600; font-size: 20px;
    color: var(--sky); letter-spacing: 1px; text-transform: uppercase;
  }
  .divider { position: absolute; left: 290px; top: 46px; width: 1px; height: 150px; background: var(--rule); }
  .contact { position: absolute; left: 318px; top: 66px; font-family: "Open Sans", sans-serif; }
  .contact__name { font-weight: 700; font-size: 23px; color: var(--ocean); text-transform: uppercase; letter-spacing: .5px; margin-bottom: 12px; }
  .contact__row { display: flex; align-items: center; gap: 9px; font-size: 14px; color: var(--ocean); line-height: 22px; }
  .contact__row svg { width: 13px; height: 13px; flex: none; }
</style>
</head>
<body>
<main class="canvas">

  <section class="card card--back" aria-label="Card back">
    <svg class="wave" viewBox="0 0 620 354" preserveAspectRatio="none" aria-hidden="true">
      <path d="M0 354 L0 298 C160 288 330 292 460 266 C540 250 590 236 620 220 L620 354 Z" fill="var(--deep)"/>
      <path d="M0 354 L0 306 C160 297 330 300 465 276 C545 260 592 248 620 234 L620 354 Z" fill="var(--sky)"/>
      <path d="M0 354 L0 316 C160 308 335 310 470 288 C548 274 595 262 620 250 L620 354 Z" fill="var(--ocean)"/>
    </svg>
    <div class="brand">
      <div class="brand__mark"></div>
      <div class="brand__name">Harborline Renewal</div>
      <div class="brand__tagline">Specializing in Water Damage Restoration</div>
    </div>
    <div class="website">www.HarborlineRenewal.example</div>
  </section>

  <section class="card card--front" aria-label="Card front">
    <svg class="wave" viewBox="0 0 620 354" preserveAspectRatio="none" aria-hidden="true">
      <path d="M120 354 C300 330 420 260 500 210 C550 180 590 160 620 150 L620 354 Z" fill="var(--deep)"/>
      <path d="M140 354 C320 334 430 270 510 222 C560 192 595 176 620 168 L620 354 Z" fill="var(--sky)"/>
      <path d="M170 354 C340 340 450 284 525 240 C570 214 600 200 620 194 L620 354 Z" fill="var(--card)"/>
    </svg>
    <div class="front-brand">
      <div class="front-brand__mark"></div>
      <div class="front-brand__name">Harborline Renewal</div>
    </div>
    <div class="divider"></div>
    <div class="contact">
      <div class="contact__name">Darnell Quisby</div>
      <div class="contact__row">
        <svg viewBox="0 0 16 16"><path d="M3 1l3 3-2 2c1 2 3 4 5 5l2-2 3 3-2 3C6 15 1 10 1 3z" fill="var(--ocean)"/></svg>
        <span>555-318-2046</span>
      </div>
      <div class="contact__row">
        <svg viewBox="0 0 16 16"><rect x="1" y="3" width="14" height="10" fill="none" stroke="var(--ocean)" stroke-width="1.6"/><path d="M1 3l7 6 7-6" fill="none" stroke="var(--ocean)" stroke-width="1.6"/></svg>
        <span>Darnell@HarborlineRenewal.example</span>
      </div>
      <div class="contact__row">
        <svg viewBox="0 0 16 16"><circle cx="8" cy="8" r="6.5" fill="none" stroke="var(--ocean)" stroke-width="1.5"/><path d="M1.5 8h13M8 1.5c-3 3-3 10 0 13M8 1.5c3 3 3 10 0 13" fill="none" stroke="var(--ocean)" stroke-width="1.2"/></svg>
        <span>www.HarborlineRenewal.example</span>
      </div>
    </div>
  </section>

</main>
</body>
</html>
```